Advertising company unique advertising platform

we need a logo design for a new company based in Australia Melbourne. We develop innovated advertising platform where consumer can use this platform to get regular discount, as business owner they can use this platform for free advertisement. Payment for this advertisement platform only payable every two weeks, when I generate revenue for their business

Industry/Entity Type

Advertising

Contact Information for Business Card

Dale Morven | Co-Founder |Managing Director
Suite 718 240 Wattlebrook Lane Melbourne Vic 3000

ABN 38 614 207 923
Tel: +61 0487 259 318 | Email: dale.morven@plivorantu.com

Font styles to use
Decorative
Script

Requirements
Must have
• Try few different design and some round corner business card
Should not have
• One round corner business card...try 4 different colour background not only black, make sure two side is designed. Be creative so imagine you are giving this to a client make sure has wow factor, if you can also try one design with engrave like all the logo, words look 3d feel
• The word Advertising Platform use attached file font

```html
<!DOCTYPE html>
<html lang="en">
<head>
<meta charset="utf-8">
<title>Kelvara Hub — Business Card</title>
<link rel="stylesheet" href="https://fonts.googleapis.com/css2?family=Cinzel:wght@400;700&family=Open+Sans:wght@400;600&display=swap">
<style>
  :root {
    --backdrop: #e7e4df;
    --card: #2b2b2c;
    --card-edge: #232324;
    --ink: #f2f2f2;
    --orange: #f2811f;
    --orange-deep: #e8541f;
    --teal: #7fc9b8;
    --shadow: rgba(0, 0, 0, 0.28);
  }
  * { box-sizing: border-box; margin: 0; padding: 0; }
  html, body { width: 1200px; height: 900px; overflow: hidden; }
  body { background: var(--backdrop); position: relative; }

  .card {
    position: absolute;
    width: 540px;
    height: 310px;
    border-radius: 22px;
    background: linear-gradient(135deg, #333334 0%, var(--card) 55%, var(--card-edge) 100%);
    box-shadow: 0 14px 30px var(--shadow);
    overflow: hidden;
  }
  .card--front { left: 110px; top: 100px; }
  .card--back  { left: 550px; top: 490px; }

  .brand {
    display: flex;
    align-items: center;
    gap: 14px;
    font-family: "Cinzel", serif;
    font-weight: 700;
    color: var(--teal);
    letter-spacing: 0.04em;
    white-space: nowrap;
  }
  .brand__dot {
    border-radius: 50%;
    background: var(--orange);
    flex: none;
  }
  .card--front .brand {
    position: absolute;
    left: 50%; top: 50%;
    transform: translate(-50%, -50%);
    font-size: 40px;
  }
  .card--front .brand__dot { width: 34px; height: 34px; }

  .card--back .brand {
    position: absolute;
    left: 40px; top: 40px;
    font-size: 34px;
  }

  .brand-mark {
    position: absolute;
    right: 50px; top: 50px;
    width: 170px; height: 170px;
    border-radius: 50%;
    background: radial-gradient(circle at 40% 35%, #f9a23b 0%, var(--orange) 55%, var(--orange-deep) 100%);
  }

  .contact {
    position: absolute;
    left: 40px; top: 120px;
    font-family: "Open Sans", sans-serif;
    color: var(--ink);
    font-size: 13.5px;
    line-height: 1.45;
  }
  .contact__name {
    font-family: "Cinzel", serif;
    font-weight: 400;
    color: var(--orange);
    font-size: 24px;
    letter-spacing: 0.03em;
    line-height: 1.1;
  }
  .contact__role {
    font-family: "Cinzel", serif;
    font-size: 10px;
    letter-spacing: 0.06em;
    margin-bottom: 6px;
  }
  .contact__label { color: var(--orange); font-weight: 600; }
  .contact__line { display: flex; align-items: center; gap: 8px; }
  .contact__icon { width: 11px; height: 11px; flex: none; }

  .accent-bar {
    position: absolute;
    left: 0; bottom: 0;
    width: 8px; height: 150px;
    background: var(--orange);
  }
</style>
</head>
<body>

  <section class="card card--front" aria-label="Card front">
    <div class="brand"><span class="brand__dot"></span>Kelvara Hub</div>
  </section>

  <section class="card card--back" aria-label="Card back">
    <div class="brand">Kelvara Hub</div>
    <div class="brand-mark" aria-hidden="true"></div>

    <div class="contact">
      <p class="contact__name">DALE MORVEN</p>
      <p class="contact__role">| CO-FOUNDER | MANAGING DIRECTOR</p>
      <p>Suite 718 240 Wattlebrook Lane</p>
      <p>Melbourne Vic 3000</p>
      <p><span class="contact__label">ABN:</span> 38 614 207 923</p>
      <p class="contact__line">
        <svg class="contact__icon" viewBox="0 0 24 24" aria-hidden="true"><path fill="#f2811f" d="M6.6 10.8a15.1 15.1 0 0 0 6.6 6.6l2.2-2.2a1 1 0 0 1 1-.25 11.4 11.4 0 0 0 3.6.57 1 1 0 0 1 1 1V20a1 1 0 0 1-1 1A17 17 0 0 1 3 4a1 1 0 0 1 1-1h3.5a1 1 0 0 1 1 1c0 1.25.2 2.45.57 3.57a1 1 0 0 1-.25 1z"/></svg>
        +61 0487 259 318
      </p>
      <p class="contact__line">
        <svg class="contact__icon" viewBox="0 0 24 24" aria-hidden="true"><rect x="2" y="5" width="20" height="14" rx="2" fill="none" stroke="#f2811f" stroke-width="2.5"/><path d="M3 6l9 7 9-7" fill="none" stroke="#f2811f" stroke-width="2.5"/></svg>
        dale.morven@plivorantu.com
      </p>
    </div>
    <div class="accent-bar"></div>
  </section>

</body>
</html>
```